The design should look similar to the uploaded example to accommodate the information needed for a business card template. I would like to see the colors orange and charcoal grey incorporated along with the logo.The following should be on the back of the card SPECIALIZING IN NEW AND USED TIRES & WHEELS FOR:- Loaders- Skid Steers- Telehandlers- Boom Lifts- Forklifs and moreELIMINATING DOWNTIMEWheel Exchange Program for New & Used Foam Filled and Solid Rubber TiresSPECIALTY SERVICES- Foam Filling Tires- Largest Tire Press in SE- ONSITE Forklift Tire Press- Boom Truck Services - Rubber Tracks

Target Market(s)

New and Existing Customers

Industry/Entity Type

Business

Contact Information for Business Card

NAMEHEAVY DUTY TIRE, LLC8470 Belvedere RoadWest Palm Beach, FL 33411P: 844-HD-TIRESF: 561-431-6469C:E: W: WWW.GRANITERIMSUPPLY-EXAMPLE.COM

Font styles to use
Sans Serif

Colors
f37122
333333

Requirements
Must have
• The logo and the information indicated for the backside of the card
Nice to have
• Keep the orange and charcoal grey colors

```html
<!DOCTYPE html>
<html lang="en">
<head>
<meta charset="utf-8">
<title>Granite Rim Supply LLC – Business Card</title>
<link rel="stylesheet" href="https://fonts.googleapis.com/css2?family=Alfa+Slab+One&family=Arimo:wght@400;700&display=swap">
<style>
  :root {
    --orange: #f37122;
    --charcoal: #333333;
    --slate-dark: #2f3a44;
    --slate-light: #4a5763;
    --paper: #ffffff;
    --ink: #3e3e3e;
    --name-grey: #5a6670;
    --stage: #e9e6e1;
  }
  * { box-sizing: border-box; margin: 0; padding: 0; }
  html, body { width: 1200px; height: 950px; overflow: hidden; }
  body {
    background: var(--stage);
    font-family: "Arimo", Arial, sans-serif;
    position: relative;
  }
  .card {
    position: absolute;
    left: 250px;
    width: 700px;
    height: 400px;
    overflow: hidden;
    box-shadow: 0 6px 18px rgba(0,0,0,.18);
  }

  /* ---------- Back side ---------- */
  .card--back {
    top: 45px;
    background: linear-gradient(160deg, var(--slate-light) 0%, var(--slate-dark) 70%);
    color: #ffffff;
  }
  .back__brand {
    position: absolute;
    left: 150px; top: 38px;
    display: flex; align-items: center; gap: 22px;
  }
  .brand-dot {
    width: 86px; height: 86px; border-radius: 50%;
    background: var(--orange);
    flex: none;
  }
  .back__name {
    font-family: "Alfa Slab One", Georgia, serif;
    font-size: 32px; line-height: 1.05;
    color: #ffffff;
    letter-spacing: .5px;
  }
  .back__content {
    position: absolute;
    left: 40px; right: 40px; top: 155px;
    text-align: center;
  }
  .back__heading {
    font-weight: 700; font-size: 19px; letter-spacing: .4px;
    margin-top: 14px;
  }
  .back__heading:first-child { margin-top: 0; }
  .back__line { font-size: 17px; margin-top: 6px; color: #e8ecef; }
  .dot { color: var(--orange); font-weight: 700; margin: 0 6px; }

  /* ---------- Front side ---------- */
  .card--front {
    top: 505px;
    background: var(--paper);
  }
  .front__band {
    position: absolute;
    left: 62px; top: 70px; bottom: 0;
    width: 78px;
    background: var(--orange);
  }
  .front__dot {
    position: absolute;
    left: 46px; top: 22px;
    width: 110px; height: 110px; border-radius: 50%;
    background: var(--charcoal);
  }
  .front__name {
    position: absolute;
    left: 178px; top: 36px;
    font-family: "Alfa Slab One", Georgia, serif;
    font-size: 34px; line-height: 1.05;
    color: var(--charcoal);
    letter-spacing: .5px;
  }
  .contact {
    position: absolute;
    left: 182px; top: 158px;
    list-style: none;
    font-size: 21px; line-height: 29px;
    color: var(--ink);
  }
  .icon {
    position: absolute;
    left: 90px;
    width: 22px; height: 22px;
    fill: var(--charcoal);
  }
  .person {
    position: absolute;
    right: 48px; top: 236px;
    text-align: left;
  }
  .person__name { font-weight: 700; font-size: 24px; color: var(--name-grey); letter-spacing: .5px; }
  .person__title { font-size: 19px; color: var(--orange); letter-spacing: .5px; margin-top: 2px; }
</style>
</head>
<body>

<section class="card card--back" aria-label="Business card back">
  <div class="back__brand">
    <span class="brand-dot"></span>
    <div class="back__name">GRANITE RIM<br>SUPPLY LLC</div>
  </div>
  <div class="back__content">
    <p class="back__heading">SPECIALIZING IN NEW AND USED TIRES &amp; WHEELS FOR</p>
    <p class="back__line">Loaders<span class="dot">•</span>Skid Steers<span class="dot">•</span>Telehandlers<span class="dot">•</span>Boom Lifts<span class="dot">•</span>Forklifs and more</p>
    <p class="back__heading">ELIMINATING DOWNTIME</p>
    <p class="back__line">Wheel Exchange Program for New &amp; Used Foam Filled and Solid Rubber Tires</p>
    <p class="back__heading">SPECIALTY SERVICES</p>
    <p class="back__line">Foam Filling Tires<span class="dot">•</span>Largest Tire Press in SE<span class="dot">•</span>ONSITE Forklift Tire Press</p>
    <p class="back__line">Boom Truck Services<span class="dot">•</span>Rubber Tracks</p>
  </div>
</section>

<section class="card card--front" aria-label="Business card front">
  <div class="front__band"></div>
  <div class="front__dot"></div>
  <div class="front__name">GRANITE RIM<br>SUPPLY LLC</div>

  <svg class="icon" style="top:163px" viewBox="0 0 24 24" aria-hidden="true"><path d="M12 2a7 7 0 0 0-7 7c0 5 7 13 7 13s7-8 7-13a7 7 0 0 0-7-7zm0 9.5A2.5 2.5 0 1 1 12 6.5a2.5 2.5 0 0 1 0 5z"/></svg>
  <svg class="icon" style="top:221px" viewBox="0 0 24 24" aria-hidden="true"><path d="M6.6 10.8a15 15 0 0 0 6.6 6.6l2.2-2.2a1 1 0 0 1 1-.25 11.4 11.4 0 0 0 3.6.57 1 1 0 0 1 1 1V20a1 1 0 0 1-1 1A17 17 0 0 1 3 4a1 1 0 0 1 1-1h3.5a1 1 0 0 1 1 1c0 1.25.2 2.45.57 3.57a1 1 0 0 1-.25 1z"/></svg>
  <svg class="icon" style="top:250px" viewBox="0 0 24 24" aria-hidden="true"><path d="M7 1h10a2 2 0 0 1 2 2v18a2 2 0 0 1-2 2H7a2 2 0 0 1-2-2V3a2 2 0 0 1 2-2zm0 3v14h10V4zm5 15.5a1 1 0 1 0 0 2 1 1 0 0 0 0-2z"/></svg>
  <svg class="icon" style="top:279px" viewBox="0 0 24 24" aria-hidden="true"><path d="M6 2h10l2 2v4H6zm-2 8h16a2 2 0 0 1 2 2v7h-4v3H6v-3H2v-7a2 2 0 0 1 2-2zm4 7v3h8v-3z"/></svg>
  <svg class="icon" style="top:308px" viewBox="0 0 24 24" aria-hidden="true"><path d="M2 5h20v14H2zm2 2v.5l8 5 8-5V7zm0 3v7h16v-7l-8 5z"/></svg>
  <svg class="icon" style="top:337px" viewBox="0 0 24 24" aria-hidden="true"><path d="M12 2a10 10 0 1 0 0 20 10 10 0 0 0 0-20zm6.9 6h-2.9a15 15 0 0 0-1.4-3.6A8 8 0 0 1 18.9 8zM12 4c.8 1.2 1.5 2.5 1.9 4h-3.8c.4-1.5 1.1-2.8 1.9-4zM4.3 14a8 8 0 0 1 0-4h3.4a16 16 0 0 0 0 4zm.8 2h2.9a15 15 0 0 0 1.4 3.6A8 8 0 0 1 5.1 16zM8 8H5.1a8 8 0 0 1 4.3-3.6C8.8 5.5 8.3 6.7 8 8zm4 12c-.8-1.2-1.5-2.5-1.9-4h3.8c-.4 1.5-1.1 2.8-1.9 4zm2.3-6H9.7a14 14 0 0 1 0-4h4.6a14 14 0 0 1 0 4zm.3 5.6c.6-1.1 1.1-2.3 1.4-3.6h2.9a8 8 0 0 1-4.3 3.6zm1.7-5.6a16 16 0 0 0 0-4h3.4a8 8 0 0 1 0 4z"/></svg>

  <ul class="contact">
    <li>5126 Marston Lane</li>
    <li>West Palm Beach, FL 33411</li>
    <li>844-GR-WHEEL</li>
    <li>836 415 2270</li>
    <li>561-278-9053</li>
    <li>name@graniterim-example.com</li>
    <li>www.graniterimsupply-example.com</li>
  </ul>

  <div class="person">
    <p class="person__name">DANA WHITLOW</p>
    <p class="person__title">PRESIDENT</p>
  </div>
</section>

</body>
</html>
```